New Wix logo and website layout

I need a new logo design and a new, modern website layout design. I am a professional therapist providing remedial massage. I am Canadian but live in Australia & would like the logo to have a somewhat 'Canadian feel' to it (something subtle i.e. no flags) I currently have a maple tree leaf as my logo. my current website is tidewaterbodywork.com.au. I need the website to work on mobile phones & traditional web browsers.

Target Market(s)

customers looking for remedial massage and manual lymphatic drainage

Industry/Entity Type

professional massage

Coding

Coded - Design and coding required

Font styles to use
Sans Serif

Colors
EB3D1F
EC4F4E
F09395
F8D3D4
FCEDEE

Requirements
Nice to have
• something subtle that indicates that I am canadian
Should not have
• no flags. nothing too bold

```html
<!DOCTYPE html>
<html lang="en">
<head>
<meta charset="utf-8">
<title>Tidewater Bodywork – Remedial Massage</title>
<link href="https://fonts.googleapis.com/css2?family=Libre+Baskerville:ital,wght@0,400;0,700;1,400&family=Poppins:wght@400;500;600&display=swap" rel="stylesheet">
<style>
:root{
  --red:#EB3D1F;
  --coral:#EC4F4E;
  --rose:#F09395;
  --blush:#F8D3D4;
  --mist:#FCEDEE;
  --ink:#222;
  --white:#fff;
}
*{box-sizing:border-box;margin:0;padding:0}
html,body{width:1200px;height:3381px;overflow:hidden}
body{position:relative;font-family:'Poppins',sans-serif;color:var(--ink);background:var(--white)}
.abs{position:absolute}

/* top bar */
.topbar{left:0;top:0;width:1200px;height:52px;background:var(--coral);color:var(--white)}
.social{display:flex;gap:20px;align-items:center}
.social span{width:22px;height:22px;border-radius:50%;background:var(--white);display:block}
.topbar .social{position:absolute;left:75px;top:15px}
.topbar .info{position:absolute;right:74px;top:13px;font-size:19px;display:flex;gap:22px;align-items:center}
.topbar .info svg{vertical-align:-3px;margin-right:8px}

/* header */
.header{left:0;top:52px;width:1200px;height:105px;background:var(--white)}
.brand{position:absolute;left:75px;top:18px;display:flex;align-items:center;gap:16px}
.brand-dot{width:58px;height:58px;border-radius:50%;background:var(--coral)}
.brand-name{font-family:'Libre Baskerville',serif;font-weight:700;font-size:28px;line-height:34px;color:#2b2b2b;letter-spacing:1px}
.nav{position:absolute;right:74px;top:44px;display:flex;gap:37px;font-family:'Libre Baskerville',serif;font-weight:700;font-size:15px;letter-spacing:.5px;color:#2b2b2b}
.nav .active{color:var(--coral)}

/* hero */
.hero{left:0;top:157px;width:1200px;height:677px;background:linear-gradient(100deg,#e9cdb4 0%,#c79a7c 45%,#8a5d46 75%,#5a3b2e 100%)}
.hero h1{position:absolute;left:75px;top:190px;font-family:'Libre Baskerville',serif;font-weight:700;font-size:64px;line-height:60px;color:var(--white);letter-spacing:2px}
.hero p{position:absolute;left:75px;top:325px;font-family:'Libre Baskerville',serif;font-style:italic;font-size:28px;line-height:39px;color:var(--white);letter-spacing:1px}
.btn{display:flex;align-items:center;justify-content:center;width:178px;height:55px;background:var(--coral);color:var(--white);font-family:'Libre Baskerville',serif;font-weight:700;font-size:18px;letter-spacing:1px}
.hero .btn{position:absolute;left:75px;top:430px}
.dots{position:absolute;left:75px;top:603px;display:flex;gap:13px}
.dots span{width:13px;height:13px;border-radius:50%;background:var(--coral)}
.dots span:first-child{background:var(--white)}

/* hexagons */
.hex{clip-path:polygon(50% 0,100% 25%,100% 75%,50% 100%,0 75%,0 25%)}
.hex-frame{background:var(--red);padding:9px}
.photo{width:100%;height:100%}

/* welcome */
.welcome-hex{left:75px;top:913px;width:420px;height:483px;padding:14px}
.welcome-hex .photo{background:linear-gradient(135deg,#f5b8a8,#e85a40 55%,#c22a12)}
h2.title{font-family:'Libre Baskerville',serif;font-weight:700;font-size:40px;line-height:46px;color:var(--coral);letter-spacing:1.5px}
.welcome h2{position:absolute;left:575px;top:965px;font-size:36px;letter-spacing:1px}
.copy{font-size:15.5px;line-height:29px;color:#333}
.welcome .copy{position:absolute;left:575px;top:1073px;width:545px}
.welcome .copy p+p{margin-top:10px}
.welcome .btn{position:absolute;left:575px;top:1280px}

/* services */
.services{left:0;top:1467px;width:1200px;height:562px;background:linear-gradient(180deg,#fce3df 0%,var(--mist) 40%,var(--blush) 100%)}
.services h2{position:absolute;left:0;width:1200px;top:76px;text-align:center}
.svc{position:absolute;top:159px;width:241px;text-align:center}
.svc .hex-frame{width:241px;height:278px;padding:8px}
.svc .photo{background:linear-gradient(160deg,#f1d5c4,#c99479)}
.svc h3{margin-top:26px;font-family:'Libre Baskerville',serif;font-weight:700;font-size:19px;color:var(--coral);letter-spacing:1px}

/* remedial */
.remedial h2{position:absolute;left:79px;top:2180px}
.remedial .copy{position:absolute;left:76px;top:2244px;width:590px}
.remedial .btn{position:absolute;left:75px;top:2445px}
.remedial-hex{left:701px;top:2101px;width:426px;height:488px;background:linear-gradient(150deg,#8a6553,#d9a88a 45%,#f0d2bd)}

/* contact */
.contact{left:0;top:2652px;width:1200px;height:588px;background:linear-gradient(120deg,#d9361c,#e8503a 50%,#c92d16);color:var(--white)}
.contact h2{position:absolute;color:var(--white);top:92px}
.item{position:absolute;left:75px;display:flex;align-items:center;gap:20px;font-size:20px}
.icon{width:54px;height:54px;border-radius:50%;border:2px solid var(--white);display:flex;align-items:center;justify-content:center;flex:none}
.item strong{font-weight:600;font-size:23px;display:block;line-height:30px}
.contact .social{position:absolute;left:75px;top:477px;gap:26px}
.contact .social span{width:24px;height:24px}
.field{position:absolute;background:var(--white);color:#333;font-size:14px;padding:16px 12px}
.field svg{position:absolute;right:16px;top:20px}
.submit{position:absolute;left:616px;top:444px;width:248px;height:56px;background:var(--rose);color:var(--white);display:flex;align-items:center;justify-content:center;font-family:'Libre Baskerville',serif;font-weight:700;font-size:18px;letter-spacing:1px}

/* footer */
.footer{left:0;top:3240px;width:1200px;height:141px;background:var(--white)}
.footer .nav{left:76px;right:auto;top:43px;gap:37px;font-size:15px}
.copyright{position:absolute;left:76px;top:83px;font-size:13px;color:#333}
.member{position:absolute;left:902px;top:20px;font-size:16px;color:var(--coral)}
.badge{position:absolute;left:877px;top:49px;width:250px;height:62px;border-radius:6px;background:linear-gradient(90deg,#a6cf3a 0 36%,#7b7f86 36% 100%)}
</style>
</head>
<body>

<div class="abs topbar">
  <div class="social" aria-label="Social links"><span></span><span></span><span></span><span></span><span></span></div>
  <div class="info">
    <span><svg width="16" height="18" viewBox="0 0 16 18"><path d="M4 1l3 4-2 2c1 3 3 5 6 6l2-2 3 3-2 3C7 17 1 11 1 4z" fill="#fff"/></svg>0400 555 218</span>
    <span><svg width="20" height="14" viewBox="0 0 20 14"><rect width="20" height="14" rx="1" fill="#fff"/><path d="M1 1l9 7 9-7" stroke="#EC4F4E" stroke-width="1.6" fill="none"/></svg>marnie@tidewaterbodywork.com.au</span>
  </div>
</div>

<header class="abs header">
  <div class="brand"><span class="brand-dot"></span><div class="brand-name">TIDEWATER<br>BODYWORK</div></div>
  <nav class="nav"><span class="active">HOME</span><span>REMEDIAL MASSAGE</span><span>ABOUT ME</span><span>FEES</span><span>CONTACT</span></nav>
</header>

<section class="abs hero" role="img" aria-label="Photo of a woman relaxing during a hot stone massage with white orchids">
  <h1>TIDEWATER<br>BODYWORK</h1>
  <p>I am a Professional Therapist Providing<br>Remedial Massage.</p>
  <a class="btn">READ MORE</a>
  <div class="dots"><span></span><span></span><span></span><span></span></div>
</section>

<section class="welcome">
  <div class="abs hex hex-frame welcome-hex"><div class="hex photo" role="img" aria-label="Red-toned photo of a client receiving a massage"></div></div>
  <h2 class="title">WELCOME TO<br>TIDEWATER BODYWORK</h2>
  <div class="copy">
    <p>I completed my training in Toronto, Canada in 1999 where I obtained a Diploma of Remedial Massage through the Northern College of Massage &amp; Hydrotherapy.</p>
    <p>Over the years, I have practiced in several different settings including medical centre, chiropractic clinic, spa and currently am a sole trader in my own practice.</p>
  </div>
  <a class="btn">READ MORE</a>
</section>

<section class="abs services">
  <h2 class="title">OUR SERVICE OFFERS</h2>
  <div class="svc" style="left:75px"><div class="hex hex-frame"><div class="hex photo" role="img" aria-label="Photo of a therapist stretching a client's arm"></div></div><h3>REMEDIAL</h3></div>
  <div class="svc" style="left:344px"><div class="hex hex-frame"><div class="hex photo" role="img" aria-label="Photo of hands massaging a client's back"></div></div><h3>DEEP TISSUE</h3></div>
  <div class="svc" style="left:617px"><div class="hex hex-frame"><div class="hex photo" role="img" aria-label="Photo of a shoulder massage"></div></div><h3>THERAPEUTIC</h3></div>
  <div class="svc" style="left:886px"><div class="hex hex-frame"><div class="hex photo" role="img" aria-label="Photo of a pregnancy massage"></div></div><h3>PREGNANCY</h3></div>
</section>

<section class="remedial">
  <h2 class="title">REMEDIAL MASSAGE</h2>
  <p class="copy">Remedial massage is used to help relieve tension and stress in the soft tissues of the body including muscles, tendons, ligaments and&nbsp; connective tissue. It helps to alleviate soft tissue discomfort associated with everyday and occupational stress, over-use injuries e.g. tendinitis, and many chronic pain conditions.&nbsp; An increase in circulation and increased joint flexibility are additional benefits.</p>
  <a class="btn">READ MORE</a>
  <div class="abs hex remedial-hex" role="img" aria-label="Photo of a woman receiving a back massage with yellow orchids"></div>
</section>

<section class="abs contact" role="region" aria-label="Contact">
  <h2 class="title" style="left:77px">CONTACT<br>INFORMATION</h2>
  <h2 class="title" style="left:614px">QUICK<br>CONTACT FORM</h2>
  <div class="item" style="top:203px"><span class="icon"><svg width="20" height="22" viewBox="0 0 20 22"><path d="M10 1a7 7 0 0 0-7 7c0 5 7 13 7 13s7-8 7-13a7 7 0 0 0-7-7z" fill="#fff"/><circle cx="10" cy="8" r="2.6" fill="#e14a33"/></svg></span><div><strong>Marnie Holt</strong>24 Harbour Lane Seaford VIC 3198</div></div>
  <div class="item" style="top:288px"><span class="icon"><svg width="18" height="18" viewBox="0 0 16 18"><path d="M4 1l3 4-2 2c1 3 3 5 6 6l2-2 3 3-2 3C7 17 1 11 1 4z" fill="#fff"/></svg></span>0400 555 218</div>
  <div class="item" style="top:376px"><span class="icon"><svg width="20" height="14" viewBox="0 0 20 14"><rect width="20" height="14" rx="1" fill="#fff"/><path d="M1 1l9 7 9-7" stroke="#e14a33" stroke-width="1.6" fill="none"/></svg></span>marnie@tidewaterbodywork.com.au</div>
  <div class="social" aria-label="Social links"><span></span><span></span><span></span><span></span><span></span></div>

  <div class="field" style="left:616px;top:191px;width:248px;height:56px">Name</div>
  <div class="field" style="left:878px;top:191px;width:249px;height:56px">Email Address</div>
  <div class="field" style="left:616px;top:260px;width:248px;height:58px">Phone No</div>
  <div class="field" style="left:878px;top:260px;width:249px;height:58px">Select Date<svg width="12" height="12" viewBox="0 0 12 12"><rect x="1" y="2" width="10" height="9" fill="none" stroke="#333"/><path d="M1 5h10M4 1v2M8 1v2" stroke="#333"/></svg></div>
  <div class="field" style="left:616px;top:332px;width:511px;height:98px">Message</div>
  <div class="submit">SUBMIT</div>
</section>

<footer class="abs footer">
  <nav class="nav"><span class="active">HOME</span><span>REMEDIAL MASSAGE</span><span>ABOUT ME</span><span>FEES</span><span>CONTACT</span></nav>
  <p class="copyright">Copyright© 2022 Company Name&nbsp; All Right Reserved</p>
  <span class="member">Member</span>
  <div class="badge" aria-label="Professional association membership badge"></div>
</footer>

</body>
</html>
```